General contractor/GM consaltant business card

I need a card for my contracting company in North Dakota, we build industrial buildings for the oil feild and oil feild related companies offices, shops, airplain hangars, airports ext. We have a familly atmosphere on the job and are very relational and personal.
Industry/Entity Type
Industrial
Contact Information for Business Card
Ridgepost Contractors LLC.
Derek T.Holloway
4837 Tamarind dr. Colorado Springs, CO. 80917
Cell# 406-555-0148
derek@ridgepostcontractors.com

```html
<!DOCTYPE html>
<html lang="en">
<head>
<meta charset="utf-8">
<title>Ridgepost Contractors LLC. – Business Card</title>
<link rel="stylesheet" href="https://fonts.googleapis.com/css2?family=Marcellus&family=Roboto:wght@300&display=swap">
<style>
  :root {
    --page-bg: #e6e7eb;
    --card-light: #f6f6f8;
    --card-mid: #cfd1e2;
    --card-deep: #4a5c9c;
    --brand-red: #e3242b;
    --brand-blue: #2f5fae;
    --contact-text: #ffffff;
    --shadow: rgba(30, 40, 80, 0.28);
  }
  * { margin: 0; padding: 0; box-sizing: border-box; }
  html, body {
    width: 1200px;
    height: 858px;
    overflow: hidden;
    background: var(--page-bg);
  }
  .canvas {
    position: relative;
    width: 1200px;
    height: 858px;
  }
  .business-card {
    position: absolute;
    width: 680px;
    height: 389px;
    border-radius: 4px;
    box-shadow: 0 14px 32px var(--shadow);
    overflow: hidden;
  }
  .card-front {
    left: 70px;
    top: 30px;
    background: linear-gradient(180deg,
      var(--card-light) 0%,
      var(--card-light) 18%,
      var(--card-mid) 58%,
      var(--card-deep) 100%);
  }
  .card-back {
    left: 450px;
    top: 440px;
    background: linear-gradient(200deg,
      var(--card-light) 0%,
      var(--card-light) 30%,
      var(--card-mid) 65%,
      var(--card-deep) 100%);
  }
  .brand-lockup {
    position: absolute;
    display: flex;
    align-items: center;
    gap: 12px;
    white-space: nowrap;
  }
  .brand-square {
    flex: none;
    background: var(--brand-blue);
  }
  .company-name {
    font-family: "Marcellus", serif;
    font-weight: 400;
    color: var(--brand-red);
    line-height: 1;
  }
  .card-front .brand-lockup {
    left: 62px;
    top: 96px;
  }
  .card-front .brand-square { width: 44px; height: 44px; }
  .card-front .company-name { font-size: 38px; }
  .card-back .brand-lockup {
    left: 50%;
    top: 50%;
    transform: translate(-50%, -50%);
    gap: 14px;
  }
  .card-back .brand-square { width: 56px; height: 56px; }
  .card-back .company-name { font-size: 42px; }
  .person-name {
    position: absolute;
    left: 330px;
    top: 160px;
    font-family: "Roboto", sans-serif;
    font-weight: 300;
    font-size: 20px;
    color: var(--brand-red);
  }
  .contact-list {
    position: absolute;
    left: 70px;
    top: 268px;
    list-style: none;
    font-family: "Roboto", sans-serif;
    font-weight: 300;
    font-size: 16px;
    color: var(--contact-text);
  }
  .contact-item {
    display: flex;
    align-items: center;
    gap: 12px;
    height: 30px;
  }
  .contact-icon {
    width: 16px;
    height: 16px;
    flex: none;
    fill: var(--brand-red);
  }
</style>
</head>
<body>
  <main class="canvas">
    <section class="business-card card-front" aria-label="Business card front">
      <div class="brand-lockup">
        <span class="brand-square" aria-hidden="true"></span>
        <h1 class="company-name">Ridgepost Contractors LLC.</h1>
      </div>
      <p class="person-name">Derek T.Holloway</p>
      <ul class="contact-list">
        <li class="contact-item">
          <svg class="contact-icon" viewBox="0 0 24 24" aria-hidden="true">
            <path d="M6.6 10.8a15.1 15.1 0 0 0 6.6 6.6l2.2-2.2a1 1 0 0 1 1-.25 11.4 11.4 0 0 0 3.6.57 1 1 0 0 1 1 1V20a1 1 0 0 1-1 1A17 17 0 0 1 3 4a1 1 0 0 1 1-1h3.5a1 1 0 0 1 1 1c0 1.25.2 2.45.57 3.57a1 1 0 0 1-.25 1z"/>
          </svg>
          <span>406-555-0148</span>
        </li>
        <li class="contact-item">
          <svg class="contact-icon" viewBox="0 0 24 24" aria-hidden="true">
            <path d="M12 2a7 7 0 0 0-7 7c0 5.2 7 13 7 13s7-7.8 7-13a7 7 0 0 0-7-7zm0 9.5A2.5 2.5 0 1 1 12 6.5a2.5 2.5 0 0 1 0 5z"/>
          </svg>
          <span>4837 Tamarind dr. Colorado Springs, CO. 80917</span>
        </li>
        <li class="contact-item">
          <svg class="contact-icon" viewBox="0 0 24 24" aria-hidden="true">
            <path d="M2 5h20v14H2z"/>
            <path d="M3 6l9 7 9-7" fill="none" stroke="#ffffff" stroke-width="1.6"/>
          </svg>
          <span>derek@ridgepostcontractors.com</span>
        </li>
      </ul>
    </section>

    <section class="business-card card-back" aria-label="Business card back">
      <div class="brand-lockup">
        <span class="brand-square" aria-hidden="true"></span>
        <p class="company-name">Ridgepost Contractors LLC.</p>
      </div>
    </section>
  </main>
</body>
</html>
```